Law Firm in Texas in need of new letterhead

Law Firm in Fort Worth, TX, USA named "Pell & Varnum, Attorneys-At-Law, LLP." This is a general practice law firm that mostly does Family Law and Criminal Defense work.

We are looking for a new letterhead that has a "classical" appeal, with modern elements.

Any color combination is fine, but please note that we do fax many documents, so the design must be clearly legible in Black and White.

We would like our letterhead to project a sense of professionalism, integrity, and ability.

Target Market(s)

Letterhead will be for correspondence generally with other attorneys and clients.

Industry/Entity Type

Law Firm

Logo Text

Pell & Varnum, Attorneys-At-Law, LLP.

Logo styles of interest
Pictorial/Combination Logo
Wordmark Logo
Lettermark Logo
Requirements
Nice to have
• Although not necessary, a "Texas Star" that is incorporated into the design would be a nice touch.
Should not have
• Colors that do not convert to B&W easily

```html
<!DOCTYPE html>
<html lang="en">
<head>
<meta charset="utf-8">
<title>Pell &amp; Varnum Letterhead</title>
<link href="https://fonts.googleapis.com/css2?family=Cinzel:wght@500&family=Tinos:wght@400;700&family=Montserrat:wght@400;600&display=swap" rel="stylesheet">
<style>
  :root {
    --backdrop: #d6d6d6;
    --paper: #fbfbfb;
    --firm-blue: #2f5f8c;
    --ink: #3a3a3a;
    --muted: #8c8c8c;
    --rule: #9aa8b6;
    --watermark: #ececec;
  }
  * { box-sizing: border-box; margin: 0; padding: 0; }
  html, body { width: 1200px; height: 926px; overflow: hidden; background: var(--backdrop); }
  .letterhead {
    position: absolute; left: 260px; top: 23px;
    width: 680px; height: 880px;
    background: var(--paper);
    box-shadow: 0 4px 18px rgba(0,0,0,0.12);
  }
  .firm-mark {
    position: absolute; left: 70px; top: 56px;
    display: flex; flex-direction: column; align-items: flex-start;
  }
  .firm-name-row { display: flex; align-items: center; gap: 12px; }
  .firm-square { width: 12px; height: 12px; background: var(--firm-blue); }
  .firm-name {
    font-family: "Cinzel", serif; font-weight: 500;
    font-size: 30px; letter-spacing: 1px; color: var(--firm-blue);
  }
  .firm-tagline {
    margin-top: 4px; margin-left: 24px;
    font-family: "Cinzel", serif; font-size: 11px; letter-spacing: 2px;
    color: var(--firm-blue);
    border-top: 1px solid var(--rule); padding-top: 4px;
  }
  .star-watermark {
    position: absolute; left: 180px; top: 240px;
    width: 320px; height: 300px;
    background: radial-gradient(circle at center, var(--watermark) 0%, rgba(236,236,236,0.4) 55%, rgba(251,251,251,0) 75%);
  }
  .letter-body {
    position: absolute; left: 70px; top: 190px; width: 540px;
    font-family: "Montserrat", sans-serif; font-size: 10.5px; line-height: 1.55;
    color: var(--ink);
  }
  .letter-body p { margin-bottom: 14px; }
  .closing {
    position: absolute; right: 70px; top: 520px; text-align: right;
    font-family: "Montserrat", sans-serif; font-size: 10.5px; color: var(--ink);
  }
  .signature {
    display: block; width: 130px; height: 40px; margin: 12px 0 6px auto;
    background: linear-gradient(90deg, rgba(60,90,180,0.10), rgba(60,90,180,0.22), rgba(60,90,180,0.10));
  }
  .signer { font-weight: 600; font-size: 12px; }
  .partners {
    position: absolute; right: 70px; top: 660px;
    display: flex; gap: 16px;
    font-family: "Tinos", serif; color: var(--muted); font-size: 10px; line-height: 1.45;
  }
  .partner { text-align: right; }
  .partner + .partner { text-align: left; border-left: 1px solid var(--rule); padding-left: 16px; }
  .partner-name { font-size: 12px; letter-spacing: 1px; text-transform: uppercase; }
  .partner-role { margin-bottom: 8px; }
  .firm-web { color: var(--firm-blue); font-weight: 700; margin-top: 8px; }
  .contact-strip {
    position: absolute; left: 70px; bottom: 50px;
    display: flex; gap: 16px;
    font-family: "Tinos", serif; font-weight: 700; font-size: 11px; line-height: 1.4;
    color: var(--firm-blue);
  }
  .contact-phone { border-left: 1px solid var(--rule); padding-left: 16px; }
</style>
</head>
<body>
  <main class="letterhead">
    <header class="firm-mark">
      <div class="firm-name-row">
        <span class="firm-square"></span>
        <span class="firm-name">PELL &amp; VARNUM</span>
      </div>
      <span class="firm-tagline">ATTORNEYS AT LAW, LLP</span>
    </header>

    <div class="star-watermark" role="img" aria-label="Faint Texas star watermark"></div>

    <section class="letter-body">
      <p>Lorem ipsum dolor sit amet, consectetur adipisicing elit, sed do eiusmod tempor incididunt ut labore et dolore magna aliqua. Ut enim ad minim veniam, quis nostrud exercitation ullamco laboris nisi ut aliquip ex ea commodo consequat. Duis aute irure dolor in reprehenderit in voluptate velit esse cillum dolore eu fugiat nulla pariatur. Excepteur sint occaecat cupidatat non proident, sunt in culpa qui officia deserunt mollit anim id est laborum.</p>
      <p>Sed do eiusmod tempor incididunt ut labore et dolore magna aliqua. Ut enim ad minim veniam, quis nostrud exercitation ullamco laboris nisi ut aliquip ex ea commodo consequat. Duis aute irure dolor in reprehenderit in voluptate velit esse cillum dolore eu fugiat nulla pariatur.</p>
      <p>Excepteur sint occaecat cupidatat non proident, sunt in culpa qui officia deserunt mollit anim id est laborum. Sed do eiusmod tempor incididunt ut labore et dolore magna aliqua, quis nostrud exercitation ullamco laboris nisi ut aliquip ex ea commodo.</p>
      <p>Duis aute irure dolor in reprehenderit in voluptate velit esse cillum dolore eu fugiat nulla pariatur. Excepteur sint occaecat cupidatat non proident, sunt in culpa qui officia deserunt mollit anim id est laborum.</p>
    </section>

    <div class="closing">
      <p>Yours Sincerely,</p>
      <span class="signature" role="img" aria-label="Handwritten signature"></span>
      <p class="signer">Jordan Hale</p>
    </div>

    <footer>
      <div class="partners">
        <div class="partner">
          <p class="partner-name">Nathaniel Pell</p>
          <p class="partner-role">Managing Partner</p>
          <p>- Licensed in the State of Texas</p>
          <p>- U.S. District Court</p>
          <p>(Northern District of Texas)</p>
          <p>- United States Supreme Court</p>
        </div>
        <div class="partner">
          <p class="partner-name">Lydia Grace Varnum</p>
          <p>- Licensed in the State of Texas</p>
          <p>- U.S. District Court</p>
          <p>(Northern District of Texas)</p>
          <p class="firm-web">www.pell-varnum.com</p>
        </div>
      </div>
      <div class="contact-strip">
        <address class="contact-address" style="font-style:normal">1418 West Magnolia Avenue<br>Fort Worth, Texas 76104</address>
        <div class="contact-phone">Phone: (817) 555-0142<br>Fax: (817) 555-0187</div>
      </div>
    </footer>
  </main>
</body>
</html>
```